Mosquito and outdoor pest management

The uploaded logo must be integrated as the main theme of the card. I would like it to be modern and eye catching. Maybe some backround images or light silver metallic background.
Space enough at the base for contact info to be put in- phone numbers,emails,names,website.
Space on the back for short blog and lines for hand writing..calling card.
Commercial- golf courses, schools, outdoor function properties, pre event treatments.
Residential- retirement villages, townhome complexes and general houses
Management

```html
<!DOCTYPE html>
<html lang="en">
<head>
<meta charset="utf-8">
<title>Bayline Yard Guard – Business Card</title>
<link rel="stylesheet" href="https://fonts.googleapis.com/css2?family=Cinzel:wght@400&display=swap">
<style>
  :root {
    --backdrop: #4a4a4a;
    --silver-light: #fbfbfb;
    --silver-mid: #e3e3e3;
    --silver-dark: #c4c4c4;
    --ink: #1d1d1d;
    --band: #050505;
    --accent: #e4202f;
    --paper-text: #f2f2f2;
    --rule: #6d6d6d;
  }
  * { margin: 0; padding: 0; box-sizing: border-box; }
  html, body { width: 1105px; height: 1200px; overflow: hidden; }
  body {
    background: var(--backdrop);
    font-family: "Cinzel", "Times New Roman", serif;
    position: relative;
  }
  .card {
    position: absolute;
    left: 196px;
    width: 720px;
    height: 412px;
    background: radial-gradient(ellipse at 55% 45%, var(--silver-light) 0%, var(--silver-mid) 45%, var(--silver-dark) 100%);
    box-shadow: 0 4px 14px rgba(0,0,0,.45);
    overflow: hidden;
  }
  .card--front { top: 146px; }
  .card--back  { top: 602px; }

  .brand {
    position: absolute; left: 42px; top: 60px;
    display: flex; align-items: center; gap: 16px;
    color: var(--ink); font-weight: 400;
  }
  .brand__dot { width: 22px; height: 22px; border-radius: 50%; background: var(--accent); flex: none; }
  .brand__name { font-size: 40px; line-height: 1; letter-spacing: .5px; white-space: nowrap; }
  .brand__tagline {
    position: absolute; left: 42px; top: 112px;
    color: var(--ink); font-size: 17px; letter-spacing: .3px; white-space: nowrap;
  }

  .contact-band {
    position: absolute; left: 0; right: 0; top: 247px; bottom: 0;
    background: var(--band);
  }
  .contact-list { list-style: none; position: absolute; left: 42px; top: 34px; }
  .contact-list li {
    display: flex; align-items: center; gap: 12px;
    color: var(--paper-text); font-size: 19px; height: 31px; letter-spacing: .3px; white-space: nowrap;
  }
  .contact-list svg { width: 18px; height: 18px; flex: none; }

  .person { position: absolute; right: 44px; top: 48px; text-align: right; white-space: nowrap; }
  .person__name { color: var(--accent); font-size: 29px; letter-spacing: .5px; }
  .person__role { color: var(--paper-text); font-size: 21px; margin-top: 2px; letter-spacing: .5px; }

  .note-lines { position: absolute; inset: 0; }
  .note-lines line { stroke: var(--rule); stroke-width: 1.3; stroke-dasharray: 1.5 2.5; }
  .back-mark { fill: var(--accent); }
</style>
</head>
<body>

<section class="card card--front" aria-label="Card front">
  <div class="brand">
    <span class="brand__dot" aria-hidden="true"></span>
    <span class="brand__name">Bayline Yard Guard</span>
  </div>
  <div class="brand__tagline">GARDEN AND GROUNDS INSECT SERVICES</div>

  <div class="contact-band">
    <ul class="contact-list">
      <li>
        <svg viewBox="0 0 24 24" aria-hidden="true"><path fill="var(--accent)" d="M6.6 10.8a15.1 15.1 0 0 0 6.6 6.6l2.2-2.2a1 1 0 0 1 1-.25 11.4 11.4 0 0 0 3.6.57 1 1 0 0 1 1 1V20a1 1 0 0 1-1 1A17 17 0 0 1 3 4a1 1 0 0 1 1-1h3.5a1 1 0 0 1 1 1c0 1.25.2 2.45.57 3.57a1 1 0 0 1-.25 1z"/></svg>
        555 201 4830
      </li>
      <li>
        <svg viewBox="0 0 24 24" aria-hidden="true"><rect x="2" y="5" width="20" height="14" rx="1.5" fill="var(--accent)"/><path d="M3 6.5l9 6.5 9-6.5" fill="none" stroke="var(--band)" stroke-width="1.6"/></svg>
        HELLO@BAYLINEYARD.COM
      </li>
      <li>
        <svg viewBox="0 0 24 24" aria-hidden="true"><circle cx="12" cy="12" r="10" fill="var(--accent)"/><path d="M2 12h20M12 2c3 3 3 17 0 20M12 2c-3 3-3 17 0 20" fill="none" stroke="var(--band)" stroke-width="1.4"/></svg>
        WWW.BAYLINEYARD.COM
      </li>
    </ul>
    <div class="person">
      <div class="person__name">Daniel Reyes</div>
      <div class="person__role">CEO/Founder</div>
    </div>
  </div>
</section>

<section class="card card--back" aria-label="Card back with lines for handwriting">
  <svg class="note-lines" width="720" height="410" viewBox="0 0 720 410">
    <line x1="25" y1="52"  x2="687" y2="52"/>
    <line x1="25" y1="97"  x2="687" y2="97"/>
    <line x1="25" y1="139" x2="687" y2="139"/>
    <line x1="25" y1="182" x2="687" y2="182"/>
    <line x1="25" y1="232" x2="687" y2="232"/>
    <line x1="25" y1="277" x2="473" y2="277"/>
    <line x1="25" y1="331" x2="522" y2="331"/>
    <line x1="25" y1="373" x2="522" y2="373"/>
    <circle class="back-mark" cx="600" cy="318" r="34" role="img" aria-label="Brand mark placeholder"/>
  </svg>
</section>

</body>
</html>
```